Hartwell Estates Business Cards

I would like a business card that includes myself and my partner.
Includes: Logo, office #, email, website, our names, our numbers and possibly the address. I would also like the logo to be embossed and the card to be horizontal.
There is a photo of our yard signs to give you an idea of the colors of our business.

Target Market(s)

Everyone in real estate market.
We are in a rural area. Our clientele are from all socioeconomic backgrounds.

Industry/Entity Type

Real Estate Agent

Contact Information for Business Card

Company Name: Hartwell Estates
Our Names, Titles & Cell #'s : Dana Pembrook-Broker (555).317.6624, Marla Pembrook-Realtor (555).609.1385
Office #: (555).240.3918
Website: hartwellestates-demo.com
Joint Email: pembrook@hartwellestates-demo.com
Office Address: 418B W. Calloway Ave.
Millbrook, OK. 70913

Font styles to use
Serif

Requirements
Must have
• HORIZONTAL, Logo, Myself and my partners names, Our cell #'s, our office #, our website, our email address
Nice to have
• Embossed logo, office address, our titles.

```html
<!DOCTYPE html>
<html lang="en">
<head>
<meta charset="utf-8">
<title>Hartwell Estates Business Cards</title>
<link rel="stylesheet" href="https://fonts.googleapis.com/css2?family=Montserrat:wght@400;500;600;700&display=swap">
<style>
  :root {
    --stage: #3a3a3a;
    --olive: #55502f;
    --purple: #4a1a78;
    --paper: #ffffff;
    --muted: #6b6a55;
    --icon: #4b4a3a;
  }
  * { box-sizing: border-box; margin: 0; padding: 0; }
  html, body { width: 1200px; height: 900px; overflow: hidden; }
  body {
    background: var(--stage);
    font-family: "Montserrat", Arial, sans-serif;
    position: relative;
  }
  .card {
    position: absolute;
    left: 320px;
    width: 560px;
    height: 320px;
    border-radius: 18px;
    box-shadow: 0 10px 24px rgba(0,0,0,0.45);
    overflow: hidden;
  }
  .card-back { top: 110px; background: var(--olive); }
  .card-front { top: 470px; background: var(--paper); }

  .back-brand {
    position: absolute;
    top: 110px; left: 0; right: 0;
    text-align: center;
    color: var(--purple);
    font-weight: 700;
    font-size: 40px;
    letter-spacing: 1px;
  }
  .back-url {
    position: absolute;
    bottom: 34px; left: 0; right: 0;
    text-align: center;
    color: var(--paper);
    font-size: 17px;
    letter-spacing: 0.3px;
  }
  .back-url strong { font-weight: 700; }

  .front-brand {
    position: absolute;
    left: 30px; top: 128px;
    display: flex; align-items: center; gap: 10px;
    white-space: nowrap;
  }
  .brand-dot {
    width: 28px; height: 28px; border-radius: 50%;
    background: var(--purple);
  }
  .brand-name {
    color: var(--purple);
    font-weight: 700;
    font-size: 18px;
  }

  .contacts {
    position: absolute;
    left: 262px; top: 36px;
    right: 16px;
    color: var(--purple);
    white-space: nowrap;
  }
  .person-name { font-weight: 700; font-size: 21px; line-height: 1.1; }
  .person-title { color: var(--muted); font-size: 12px; margin-top: 2px; }
  .person-phone { font-size: 14px; margin-top: 1px; }
  .person + .person { margin-top: 8px; }
  .address { font-size: 14px; line-height: 1.3; margin-top: 12px; }
  .office-lines { list-style: none; margin-top: 8px; font-size: 12.5px; }
  .office-lines li { display: flex; align-items: center; gap: 8px; line-height: 1.5; }
  .office-lines svg { width: 11px; height: 11px; flex: none; }
  .office-lines .web { font-weight: 600; }
</style>
</head>
<body>
  <section class="card card-back">
    <div class="back-brand">Hartwell Estates</div>
    <p class="back-url">www.<strong>hartwellestates-demo</strong>.com</p>
  </section>

  <section class="card card-front">
    <div class="front-brand">
      <span class="brand-dot"></span>
      <span class="brand-name">Hartwell Estates</span>
    </div>

    <div class="contacts">
      <div class="person">
        <p class="person-name">Dana Pembrook</p>
        <p class="person-title">Broker</p>
        <p class="person-phone">(555).317.6624</p>
      </div>
      <div class="person">
        <p class="person-name">Marla Pembrook</p>
        <p class="person-title">Realtor</p>
        <p class="person-phone">(555).609.1385</p>
      </div>
      <p class="address">418B W. Calloway Ave.<br>Millbrook, OK. 70913</p>
      <ul class="office-lines">
        <li>
          <svg viewBox="0 0 12 12" aria-hidden="true"><path d="M2 1h3l1 3-2 1c1 1.5 2 2.5 3 3l1-2 3 1v3c-5 0-9-4-9-9z" fill="var(--icon)"/></svg>
          (555).240.3918
        </li>
        <li>
          <svg viewBox="0 0 12 12" aria-hidden="true"><rect x="1" y="2.5" width="10" height="7" fill="none" stroke="var(--icon)" stroke-width="1.2"/><path d="M1 3l5 3.5L11 3" fill="none" stroke="var(--icon)" stroke-width="1.2"/></svg>
          pembrook@hartwellestates-demo.com
        </li>
        <li class="web">
          <svg viewBox="0 0 12 12" aria-hidden="true"><circle cx="6" cy="6" r="5" fill="none" stroke="var(--icon)" stroke-width="1.2"/><path d="M1 6h10M6 1c-2.5 3-2.5 7 0 10M6 1c2.5 3 2.5 7 0 10" fill="none" stroke="var(--icon)" stroke-width="1"/></svg>
          www.hartwellestates-demo.com
        </li>
      </ul>
    </div>
  </section>
</body>
</html>
```